Stationery Design Project

We need a stationery design for our Norwegian trucking company. We have existed for about 15 years and our 12 drivers uses relatively new vehicles to transport goods around in northern Norway. Long distance routes with fresh fish og food transport is our main operations.

We have already made alogo that's printed on our trucks. The logo and a picture of our trucks is attached. I think the logo i crappy, but since its already in use, changing it is not an option in this round. Still using a better colour scheme in the overall stationery and more interesting fonts is possible (altso in the logo).

Company details:
Name: Kjelvraket AS
Organisation nr 873 615 309
Post adress: 8642 Raudvik

I like minimalism and simplicity. I am avalibly for questions in normal GMT working hours either here or on mail: ivar@fjordlast.no

Reason: Hi. Im extending the deadline because I needed some time to find a vector file of our logo. Sorry for the inconvenience

Hi, and thanks for all your interest in the project. Some updates:

-          I have decided to commit to using one of the designs. Some designer will get the payment.

-          I have extended the deadline with 24 hours since I needed some time to find our firms vector logo (a slow Swedish man was holding me up)

-          We will not choose a design before the deadline. No need to rush.

-          We have received a lot of great design and think there is a need to specified the product we want to make:

o   Business Card for all our employers. I just need the design and will duplicate with the correct numbers and name myself. The information on should be: Logo, employer’s name, Phone number, email, website, Postal number and address. Use this as a template: logo, Leif Brattvoll, 47382066, Leif@fjordlast.no,, fjordlast.no, 8642 Raudvik. The order and placement of the information is your creative decision.

o   Stickers to put on the goods we travel. On the sticker the should be the following information: Logo, phone number, Tekst and link: Fraktæ av Kjelvraket. Ke du syns? Fjordlast.no/tilbakemelding (this means: Handled by Kjelvraket. What do you think Fjordlast.no/feedback -à the link will be a feedback form). The placement the information and size is your creative decision with some stings: we have been thinking of using Drukko for printing and see that a size about 6x6 cm, 8x5 or something like that. (with 3000 copies our budget is 200 punds). Any suggestions of other suppliers are welcome. Drukko price calculator http://www.drukkolabelhouse.co.uk/digital-litho-printing/printing-labels-tags/stickers/

o   Letterhead with logo, address, phone number and organizational number.

o   Envelopes with logo,address, phone number and organizational number.

Have a nice day.

 

 

• Using the blue colour in the logo and using a similar graphic approch.

```html
<!DOCTYPE html>
<html lang="no">
<head>
<meta charset="utf-8">
<title>Kjelvraket – visittkort</title>
<link href="https://fonts.googleapis.com/css2?family=Source+Sans+3:wght@400;600;700&display=swap" rel="stylesheet">
<style>
  :root {
    --backdrop: #9a9ea3;
    --white: #ffffff;
    --brand-blue: #0a72bb;
    --deep-blue: #0d4fa0;
    --navy: #1452a0;
    --ink: #222428;
    --edge: #c9cdd2;
    --rule: #b9bec4;
  }
  * { box-sizing: border-box; margin: 0; padding: 0; }
  html, body { width: 1200px; height: 751px; overflow: hidden; }
  body {
    position: relative;
    background: linear-gradient(135deg, #b5b9be 0%, var(--backdrop) 50%, #85898e 100%);
    font-family: "Source Sans 3", "Segoe UI", sans-serif;
  }

  .card {
    position: absolute;
    width: 525px;
    height: 300px;
    overflow: hidden;
  }
  .card--front { left: 45px;  top: 45px;  background: var(--white); border: 1px solid var(--edge); }
  .card--blue  { left: 615px; top: 45px;  background: var(--brand-blue); }
  .card--deep  { left: 45px;  top: 390px; background: var(--deep-blue); }
  .card--white { left: 615px; top: 390px; background: var(--white); border: 1px solid var(--edge); }

  .wordmark {
    position: absolute;
    left: 0; right: 0;
    top: 124px;
    text-align: center;
    font-weight: 700;
    font-size: 56px;
    line-height: 1;
  }
  .card--front .wordmark { top: 68px; color: var(--navy); }
  .card--blue .wordmark,
  .card--deep .wordmark { color: var(--white); }
  .card--white .wordmark { color: var(--navy); }

  .web-line {
    position: absolute;
    left: 0; right: 0;
    top: 249px;
    text-align: center;
    font-size: 19px;
    line-height: 22px;
    letter-spacing: 3.6px;
  }
  .card--blue .web-line,
  .card--deep .web-line { color: var(--white); }
  .card--white .web-line { color: var(--ink); }

  .contact-person {
    position: absolute;
    right: 274px;
    top: 188px;
    text-align: right;
    color: var(--ink);
    font-size: 16px;
    line-height: 22px;
  }
  .contact-person .name {
    color: var(--navy);
    font-weight: 700;
    font-size: 19px;
    line-height: 26px;
  }
  .contact-divider {
    position: absolute;
    left: 265px;
    top: 187px;
    width: 1px;
    height: 70px;
    background: var(--rule);
  }
  .contact-company {
    position: absolute;
    left: 276px;
    top: 190px;
    color: var(--ink);
    font-size: 16px;
    line-height: 22px;
  }
  .contact-company .label { color: var(--brand-blue); }

  .row { display: flex; align-items: center; gap: 5px; }
  .contact-person .row { justify-content: flex-end; }
  .icon { width: 11px; height: 11px; fill: var(--navy); flex: none; }

  .card-band { position: absolute; left: 0; bottom: 0; width: 525px; height: 10px; }
</style>
</head>
<body>

<section class="card card--front" aria-label="Visittkort forside">
  <div class="wordmark">Kjelvraket</div>

  <div class="contact-person">
    <div class="name">Leif Brattvoll</div>
    <div class="row">
      <svg class="icon" viewBox="0 0 12 12" aria-hidden="true"><path d="M1 11V5l5-3 5 3v6H8V8H4v3z"/></svg>
      <span>8642 Raudvik</span>
    </div>
    <div class="row">
      <svg class="icon" viewBox="0 0 12 12" aria-hidden="true"><path d="M3 1l2 2.5-1.2 1.3a7 7 0 0 0 3.4 3.4L8.5 7 11 9l-1.5 2C5 11 1 7 1 2.5z"/></svg>
      <span>47382066</span>
    </div>
  </div>

  <div class="contact-divider"></div>

  <div class="contact-company">
    <div><span class="label">Org nr</span> 873 615 309</div>
    <div class="row">
      <svg class="icon" viewBox="0 0 12 12" aria-hidden="true"><path d="M1 3h10v7H1z M1 3l5 4 5-4" fill="none" stroke="#1452a0" stroke-width="1.6"/></svg>
      <span>Leif@fjordlast.no</span>
    </div>
    <div class="row">
      <svg class="icon" viewBox="0 0 12 12" aria-hidden="true"><circle cx="6" cy="6" r="5" fill="none" stroke="#1452a0" stroke-width="1.2"/><path d="M1 6h10M6 1c-2.5 3-2.5 7 0 10M6 1c2.5 3 2.5 7 0 10" fill="none" stroke="#1452a0" stroke-width="1"/></svg>
      <span>www.fjordlast.no</span>
    </div>
  </div>

  <svg class="card-band" viewBox="0 0 525 10" preserveAspectRatio="none" aria-hidden="true">
    <polygon points="0,0 262,0 252,10 0,10" fill="#1452a0"/>
    <polygon points="268,0 525,0 525,10 258,10" fill="#0a72bb"/>
  </svg>
</section>

<section class="card card--blue" aria-label="Visittkort bakside, blå">
  <div class="wordmark">Kjelvraket</div>
  <div class="web-line">www.fjordlast.no</div>
</section>

<section class="card card--deep" aria-label="Visittkort bakside, mørkeblå">
  <div class="wordmark">Kjelvraket</div>
  <div class="web-line">www.fjordlast.no</div>
</section>

<section class="card card--white" aria-label="Visittkort bakside, hvit">
  <div class="wordmark">Kjelvraket</div>
  <div class="web-line">www.fjordlast.no</div>
</section>

</body>
</html>
```